Tech business card design

We need an amazing business card design for our new business 'Pexla' a marketing tech startup based in Sydney, Australia. We provide an online marketplace for businesses to search and buy advertising media, connect with service providers and learn more about marketing. We wish to communicate 'cool tech', reliability and professionalism and design based around our logo.

Target Market(s)

Business Owners

Contact Information for Business Card

Name
Position
Email Address
Website
Phone Number

Font styles to use
Other font styles liked:
• Avenir & Avenir Next

Colors

Designer to choose colors to be used in the design.

```html
<!DOCTYPE html>
<html lang="en">
<head>
<meta charset="utf-8">
<title>Pexla Business Card</title>
<link href="https://fonts.googleapis.com/css2?family=Nunito+Sans:wght@400;800&display=swap" rel="stylesheet">
<style>
  :root {
    --backdrop: #232325;
    --navy: #141c4a;
    --navy-deep: #0e1540;
    --navy-soft: #1c2658;
    --paper: #ffffff;
    --paper-tint: #f1f2f5;
    --ink-muted: #6b6f80;
  }
  * { margin: 0; padding: 0; box-sizing: border-box; }
  html, body {
    width: 1200px; height: 996px; overflow: hidden;
    background: var(--backdrop);
    font-family: "Nunito Sans", "Avenir Next", Avenir, sans-serif;
  }
  .stage {
    width: 1200px; height: 996px;
    display: flex; flex-direction: column;
    align-items: center; justify-content: center; gap: 56px;
  }
  .card {
    position: relative;
    width: 640px; height: 366px;
    border-radius: 4px; overflow: hidden;
    box-shadow: 0 12px 30px rgba(0,0,0,0.45);
  }

  /* Front */
  .card-front { background: var(--paper); color: var(--navy); }
  .front-icon-field {
    position: absolute; inset: 0;
    background: radial-gradient(ellipse at 60% 45%, var(--paper-tint) 0%, var(--paper) 75%);
  }
  .front-brand {
    position: absolute; top: 78px; right: 40px;
    display: flex; align-items: flex-end; gap: 4px;
    color: var(--navy); font-weight: 800;
  }
  .front-wordmark {
    font-size: 96px; letter-spacing: -2px; line-height: 1;
  }
  .front-wordmark-tm {
    font-size: 12px; line-height: 1; padding-bottom: 8px;
  }
  .holder {
    position: absolute; left: 40px; bottom: 40px;
  }
  .holder-name {
    font-size: 20px; font-weight: 800; letter-spacing: 0.5px; text-transform: uppercase;
  }
  .holder-role {
    font-size: 13px; font-weight: 400; color: var(--ink-muted); margin-top: 2px;
  }
  .contact-list {
    list-style: none; display: flex; gap: 16px; margin-top: 16px;
    font-size: 15px; font-weight: 400; color: var(--navy);
  }
  .contact-item { display: flex; align-items: center; gap: 6px; white-space: nowrap; }
  .contact-icon { width: 16px; height: 16px; flex: none; }

  /* Back */
  .card-back { background: var(--navy-deep); }
  .back-pattern-field {
    position: absolute; inset: 0;
    background: linear-gradient(135deg, var(--navy-soft) 0%, var(--navy-deep) 100%);
  }
  .back-wordmark {
    position: absolute; inset: 0;
    display: flex; align-items: center; justify-content: center;
    font-size: 52px; font-weight: 800; letter-spacing: -1px;
    color: var(--paper);
  }
</style>
</head>
<body>
<main class="stage">

  <section class="card card-front" aria-label="Business card front">
    <div class="front-icon-field" role="img" aria-label="Faint line-icon illustrations of marketing tools: charts, coins, search glass, puzzle pieces and gears"></div>
    <div class="front-brand">
      <span class="front-wordmark">Pexla</span>
      <span class="front-wordmark-tm">TM</span>
    </div>

    <div class="holder">
      <h1 class="holder-name">Marcus Lane</h1>
      <p class="holder-role">Managing Director</p>
      <ul class="contact-list">
        <li class="contact-item">
          <svg class="contact-icon" viewBox="0 0 16 16" aria-hidden="true">
            <circle cx="8" cy="8" r="8" fill="#141c4a"/>
            <path d="M5.5 4.5l1.4-.3.8 1.8-.9.7a5 5 0 0 0 2.5 2.5l.7-.9 1.8.8-.3 1.4c-3.6.3-6.3-2.4-6-6z" fill="#fff"/>
          </svg>
          000-555-0198
        </li>
        <li class="contact-item">
          <svg class="contact-icon" viewBox="0 0 16 16" aria-hidden="true">
            <circle cx="8" cy="8" r="8" fill="#141c4a"/>
            <rect x="4" y="5" width="8" height="6" rx="0.6" fill="#fff"/>
            <path d="M4.3 5.4L8 8.3l3.7-2.9" stroke="#141c4a" stroke-width="0.9" fill="none"/>
          </svg>
          info@pexlamail.com
        </li>
        <li class="contact-item">
          <svg class="contact-icon" viewBox="0 0 16 16" aria-hidden="true">
            <circle cx="8" cy="8" r="8" fill="#141c4a"/>
            <g stroke="#fff" stroke-width="0.9" fill="none">
              <circle cx="8" cy="8" r="4.5"/>
              <ellipse cx="8" cy="8" rx="2" ry="4.5"/>
              <path d="M3.5 8h9M4.3 5.6h7.4M4.3 10.4h7.4"/>
            </g>
          </svg>
          www.pexla.com
        </li>
      </ul>
    </div>
  </section>

  <section class="card card-back" aria-label="Business card back">
    <div class="back-pattern-field" role="img" aria-label="Tone-on-tone repeating brand pattern in dark navy"></div>
    <div class="back-wordmark">Pexla</div>
  </section>

</main>
</body>
</html>
```